K.R Landscaping 484-883-7758Mulching Mowing Planting Spring and Fall Clean up

The colors I would like to work with Are black and green.I do have a Facebook page it's https://www.examplesocial.net/KR-Landscaping-518203946172834/

For my business logo I would like to put that either on the corner or in the background

Services: mowing, mulching, fall and spring cleanup, hedge trimming

Industry/Entity Type

Landscaping

Requirements
Must have
• Please use these pics
• I like Design #9926064
• and room for addresses to
Should not have
• the pics in the back of card

```html
<!DOCTYPE html>
<html lang="en">
<head>
<meta charset="utf-8">
<title>K.R Landscaping – Postcard</title>
<link rel="stylesheet" href="https://fonts.googleapis.com/css2?family=Jost:wght@400;500&family=Roboto+Condensed:wght@400;500&family=Oswald:wght@500&display=swap">
<style>
  :root{
    --bg:#2a2a2a;
    --green:#5cb83c;
    --green-dark:#3f9a2a;
    --ink:#1e1e1e;
    --panel:#29292b;
    --white:#ffffff;
    --grey-soft:#e4e4e4;
    --text:#2b2b2b;
    --line:#555;
  }
  *{box-sizing:border-box;margin:0;padding:0}
  html,body{width:900px;height:1200px;overflow:hidden}
  body{background:var(--bg);position:relative;font-family:"Jost",sans-serif}

  .card{position:absolute;left:91px;width:704px;overflow:hidden}
  .card--front{top:38px;height:544px;background:var(--panel)}
  .card--back{top:622px;height:545px;background:var(--white)}
  .card svg.shapes{position:absolute;inset:0}

  /* front */
  .front-photo{position:absolute;inset:0;
    background:linear-gradient(180deg,#8fb8e0 0%,#b9d3ea 18%,#4f7f3a 40%,#5f8f3f 62%,#3d6a2a 100%)}
  .brand{position:absolute;left:50px;top:60px;width:220px;text-align:center;color:var(--white)}
  .brand__mark{width:70px;height:70px;border-radius:50%;border:3px solid var(--white);margin:0 auto 12px}
  .brand__name{font-family:"Oswald",sans-serif;font-weight:500;font-size:30px;letter-spacing:.5px;line-height:1}
  .brand__tag{font-size:13px;line-height:1.1;margin-top:8px}

  .services{position:absolute;left:0;top:312px;list-style:none}
  .services__title{background:var(--green);color:var(--white);width:259px;height:37px;
    font-size:29px;line-height:37px;padding-left:32px;margin-bottom:18px}
  .services__item{background:var(--green);color:var(--white);width:259px;height:31px;
    font-family:"Roboto Condensed",sans-serif;font-size:22px;line-height:31px;padding-left:32px;
    margin-bottom:11px;display:flex;align-items:center;gap:8px}
  .services__item svg{width:20px;height:20px;flex:none;margin-left:-2px}

  .thumb{position:absolute;border-radius:50%;border:5px solid var(--white)}
  .thumb--sign{left:329px;top:355px;width:133px;height:124px;
    background:linear-gradient(160deg,#6e9a55,#4c7a34 60%,#7c6a4e)}
  .thumb--bed{left:493px;top:327px;width:161px;height:158px;
    background:linear-gradient(170deg,#b8c6d8,#8aa0b8 40%,#3b3a36 70%,#c99e7a)}

  .call{position:absolute;left:290px;top:497px;color:var(--white);font-size:28px;display:flex;align-items:center;gap:10px}
  .call svg{width:26px;height:26px}

  /* back */
  .message{position:absolute;left:53px;top:40px;width:255px;font-size:18px;line-height:23px;color:var(--text)}
  .message svg{position:absolute;left:-28px;top:3px;width:18px;height:18px}
  .contact{position:absolute;left:0;top:346px;width:429px;height:130px;background:var(--green);color:var(--white);padding:8px 0 0 29px}
  .contact__title{font-size:26px;line-height:1.1;margin-bottom:3px}
  .contact__row{font-size:19px;line-height:26px;display:flex;align-items:center;gap:6px;white-space:nowrap}
  .contact__row svg{width:16px;height:16px;flex:none}
  .contact__indent{padding-left:23px}
  .follow{position:absolute;left:229px;top:50px;font-size:19px;display:flex;align-items:center;gap:8px}
  .follow span.dot{width:24px;height:24px;border-radius:50%;background:#2a9fd8;display:inline-block}
  .follow span.dot--b{background:#3a5ba0}
  .contact__phone{position:absolute;left:258px;top:96px}

  .mini-brand{position:absolute;left:488px;top:38px;width:95px;text-align:center;color:var(--ink)}
  .mini-brand__mark{width:34px;height:34px;border-radius:50%;border:2px solid var(--ink);margin:0 auto 4px}
  .mini-brand__name{font-family:"Oswald",sans-serif;font-weight:500;font-size:13px;line-height:1}
  .mini-brand__tag{font-size:7px;line-height:1.1;margin-top:2px}
  .stamp{position:absolute;left:593px;top:32px;width:83px;height:99px;border:1px solid var(--line)}
  .address-line{position:absolute;left:458px;width:217px;border-top:1px solid var(--line)}
</style>
</head>
<body>

<section class="card card--front">
  <div class="front-photo" role="img" aria-label="Photo of a mowed lawn, trees and a two-storey house with a wooden deck"></div>
  <svg class="shapes" viewBox="0 0 704 544" preserveAspectRatio="none" aria-hidden="true">
    <path d="M0 220 Q60 330 250 352 Q470 380 704 365 V544 H0Z" fill="#ffffff"/>
    <path d="M0 232 Q60 340 250 364 Q470 390 704 380 V544 H0Z" fill="var(--green)"/>
    <path d="M0 246 Q60 352 250 378 Q470 404 704 398 V544 H0Z" fill="var(--panel)"/>
  </svg>

  <div class="brand">
    <div class="brand__mark"></div>
    <div class="brand__name">K.R LANDSCAPING</div>
    <div class="brand__tag">For all your Professional<br>Landscaping Needs</div>
  </div>

  <ul class="services">
    <li class="services__title">Our Services</li>
    <li class="services__item"><svg viewBox="0 0 20 20"><circle cx="10" cy="10" r="8" fill="none" stroke="#fff" stroke-width="1.8"/><path d="M6 10.5l3 3 5-6" fill="none" stroke="#fff" stroke-width="1.8"/></svg>Mulching Mowing</li>
    <li class="services__item"><svg viewBox="0 0 20 20"><circle cx="10" cy="10" r="8" fill="none" stroke="#fff" stroke-width="1.8"/><path d="M6 10.5l3 3 5-6" fill="none" stroke="#fff" stroke-width="1.8"/></svg>Planting Plants</li>
    <li class="services__item"><svg viewBox="0 0 20 20"><circle cx="10" cy="10" r="8" fill="none" stroke="#fff" stroke-width="1.8"/><path d="M6 10.5l3 3 5-6" fill="none" stroke="#fff" stroke-width="1.8"/></svg>Fall &amp; Spring Clean up</li>
    <li class="services__item"><svg viewBox="0 0 20 20"><circle cx="10" cy="10" r="8" fill="none" stroke="#fff" stroke-width="1.8"/><path d="M6 10.5l3 3 5-6" fill="none" stroke="#fff" stroke-width="1.8"/></svg>Hedge Trimming</li>
  </ul>

  <div class="thumb thumb--sign" role="img" aria-label="Photo of a landscaped business sign on a lawn"></div>
  <div class="thumb thumb--bed" role="img" aria-label="Photo of a fresh mulch bed beside a house and patio"></div>

  <div class="call">Call Now:
    <svg viewBox="0 0 26 26"><circle cx="13" cy="13" r="11" fill="none" stroke="var(--green)" stroke-width="2"/><path d="M9 8.5c0 5 3.5 8.5 8.5 8.5l1-2-2.5-1.2-1.2 1.2c-1.6-.8-2.8-2-3.6-3.6l1.2-1.2L11 7.5z" fill="var(--green)"/></svg>
    392-615-0248</div>
</section>

<section class="card card--back">
  <svg class="shapes" viewBox="0 0 704 545" preserveAspectRatio="none" aria-hidden="true">
    <defs>
      <radialGradient id="soft" cx="0.35" cy="0.4" r="0.7">
        <stop offset="0" stop-color="#ffffff"/><stop offset="1" stop-color="#d9d9d9"/>
      </radialGradient>
    </defs>
    <path d="M0 0 H395 Q510 180 412 346 H0Z" fill="var(--ink)"/>
    <path d="M0 0 H380 Q490 180 396 346 H0Z" fill="var(--green)"/>
    <path d="M0 0 H360 Q466 180 376 346 H0Z" fill="url(#soft)"/>
    <path d="M0 476 H429 Q390 520 322 545 H0Z" fill="var(--ink)"/>
    <path d="M0 476 H412 Q370 514 300 545 H0Z" fill="var(--green)"/>
    <path d="M0 476 H396 Q350 510 280 545 H0Z" fill="url(#soft)"/>
  </svg>

  <p class="message">
    <svg viewBox="0 0 20 20"><circle cx="10" cy="10" r="8" fill="none" stroke="var(--green)" stroke-width="1.8"/><path d="M6 10.5l3 3 5-6" fill="none" stroke="var(--green)" stroke-width="1.8"/></svg>
    Lorem Ipsum is simply dummy text of the printing and typesetting industry. Lorem Ipsum has been the industry's standard dummy text ever since the 1500s, when an unknown printer took a galley of type and scrambled it to make a type specimen book.It has survived not only five centuries, but also the leap into electronic
  </p>

  <div class="contact">
    <div class="contact__title">Contact info</div>
    <div class="contact__row"><svg viewBox="0 0 16 16"><path d="M8 1a4 4 0 0 0-4 4c0 3 4 7 4 7s4-4 4-7a4 4 0 0 0-4-4zm0 5.5A1.5 1.5 0 1 1 8 3.5a1.5 1.5 0 0 1 0 3z" fill="#fff"/><path d="M3 14h10" stroke="#fff" stroke-width="1.5"/></svg>Address line 1</div>
    <div class="contact__row contact__indent">Address line 2</div>
    <div class="contact__row"><svg viewBox="0 0 16 16"><rect x="2" y="4" width="12" height="8" fill="none" stroke="#fff" stroke-width="1.3"/><path d="M2 4l6 5 6-5" fill="none" stroke="#fff" stroke-width="1.3"/></svg>yourmail@example.com</div>
    <div class="follow">Follow Us <span class="dot"></span><span class="dot dot--b"></span></div>
    <div class="contact__row contact__phone"><svg viewBox="0 0 16 16"><circle cx="8" cy="8" r="6.5" fill="none" stroke="#fff" stroke-width="1.3"/><path d="M5.5 5c0 3 2.5 5.5 5.5 5.5l.6-1.3-1.5-.7-.7.7c-1-.5-1.8-1.3-2.3-2.3l.7-.7L7 5.2z" fill="#fff"/></svg>392-615-0248</div>
  </div>

  <div class="mini-brand">
    <div class="mini-brand__mark"></div>
    <div class="mini-brand__name">K.R LANDSCAPING</div>
    <div class="mini-brand__tag">For all your Professional<br>Landscaping Needs</div>
  </div>
  <div class="stamp"></div>
  <div class="address-line" style="top:336px"></div>
  <div class="address-line" style="top:374px"></div>
  <div class="address-line" style="top:411px"></div>
</section>

</body>
</html>
```